Etikett für einen Rosé Wein
Zielgruppe
Wir sind ein Weingut und benötigen ein neues Etikett für unseren Muskattrollinger Rosé. Unsere Kunden sind eher traditionelle Weinkäufer.
Aufgabenstellung
Format:
Höhe: 9 cm
Breite: 11 cm
Da es nur ein Vorderetikett gibt, müssen alle relevanten Angaben (Hersteller, Alkohol, Inhalt in L, Rebsorte, etc.) enthalten sein. (siehe Flaschenabbildung anbei)
WÜRTTEMBERG
2019er
Muskattrollinger Rosé
DEUTSCHER QUALITÄTSWEIN
11,0 % Vol.
0,75 l
Enthält Sulfite
A.P.Nr. 58127364
Abfüller
Straße / PLZ / Ort / Tel.
Der Flaschenverschluss ist schwarz d.h. das neue Etikettendesign sollte dazu passen.
Bisher ist der Hintergrund des Weinetiketts schwarz. Dies muss jedoch nicht so bleiben.
Im Anhang finden Sie außerdem ein Plakat. Ggf. können Sie für das Flaschendesign einige nostalgische Elemente davon übernehmen.

```html
<!DOCTYPE html>
<html lang="de">
<head>
<meta charset="utf-8">
<title>Muskattrollinger Rosé – Etikett</title>
<link rel="stylesheet" href="https://fonts.googleapis.com/css2?family=Pirata+One&family=Brawler:wght@400;700&display=swap">
<style>
  :root {
    --page: #ffffff;
    --paper: #f4f4ee;
    --rose: #e6b8cc;
    --rose-line: #e2b0c8;
    --ink: #2b2b2b;
    --sketch-light: #d8d6cf;
    --sketch-dark: #8d8c88;
  }
  html, body {
    margin: 0;
    padding: 0;
    width: 728px;
    height: 1200px;
    overflow: hidden;
    background: var(--page);
  }
  .wine-label {
    position: absolute;
    left: 24px;
    top: 322px;
    width: 680px;
    height: 556px;
    display: block;
  }
  .label-paper { fill: var(--paper); }
  .frame-line { stroke: var(--rose-line); stroke-width: 2; fill: none; }
  .name-band { fill: var(--rose); }
  .ornament { fill: url(#ornamentTone); }
  .sketch { fill: url(#sketchTone); }
  .blackletter { font-family: "Pirata One", "UnifrakturCook", serif; fill: var(--ink); }
  .serif { font-family: "Brawler", Georgia, serif; fill: var(--ink); }
  .volume, .vintage { font-size: 29px; }
  .quality-arc { font-size: 19px; font-weight: 700; letter-spacing: 0.5px; }
  .region { font-size: 24px; font-weight: 700; letter-spacing: 1px; }
  .variety { font-size: 72px; }
  .legal { font-size: 19px; font-weight: 700; letter-spacing: 0.5px; }
  .bottler { font-size: 26px; font-weight: 700; letter-spacing: 1px; }
  .address { font-size: 25px; font-weight: 700; letter-spacing: 1.5px; word-spacing: 8px; }
</style>
</head>
<body>
<svg class="wine-label" viewBox="0 0 680 556" xmlns="http://www.w3.org/2000/svg">
  <defs>
    <linearGradient id="ornamentTone" x1="0" y1="0" x2="1" y2="0">
      <stop offset="0" stop-color="#f0d8e3"/>
      <stop offset="0.5" stop-color="#e8c2d4"/>
      <stop offset="1" stop-color="#f0d8e3"/>
    </linearGradient>
    <radialGradient id="sketchTone">
      <stop offset="0" stop-color="var(--sketch-dark)"/>
      <stop offset="1" stop-color="var(--sketch-light)"/>
    </radialGradient>
    <path id="qualityCurve" d="M 172 132 Q 341 30 512 132"/>
  </defs>

  <rect class="label-paper" x="0" y="0" width="680" height="556"/>

  <!-- frame -->
  <path class="frame-line" d="M 163 22 H 27 V 534 H 163"/>
  <path class="frame-line" d="M 517 22 H 653 V 534 H 517"/>

  <rect class="ornament" x="177" y="14" width="326" height="30" rx="15" role="img" aria-label="Geschwungenes Zierornament in Rosé"/>
  <rect class="ornament" x="177" y="512" width="326" height="30" rx="15" role="img" aria-label="Geschwungenes Zierornament in Rosé"/>

  <!-- header -->
  <text class="blackletter volume" x="41" y="68">11,0 % Vol.</text>
  <text class="blackletter volume" x="41" y="99">0,75 l</text>
  <text class="blackletter vintage" x="637" y="68" text-anchor="end">2019er</text>

  <text class="serif quality-arc"><textPath href="#qualityCurve" startOffset="50%" text-anchor="middle">DEUTSCHER QUALITÄTSWEIN</textPath></text>

  <ellipse class="sketch" cx="342" cy="133" rx="78" ry="30" role="img" aria-label="Skizze einer Weintraube mit Rebblatt"/>

  <text class="serif region" x="340" y="199" text-anchor="middle">WÜRTTEMBERG</text>

  <!-- variety band -->
  <rect class="name-band" x="27" y="233" width="626" height="138"/>
  <text class="blackletter variety" x="340" y="298" text-anchor="middle">Muskattrollinger</text>
  <text class="blackletter variety" x="340" y="357" text-anchor="middle">Rosé</text>

  <!-- legal -->
  <text class="serif legal" x="41" y="412">Enthält Sulfite</text>
  <text class="serif legal" x="637" y="412" text-anchor="end">A.P. Nr.58127364</text>

  <ellipse class="sketch" cx="81" cy="476" rx="40" ry="40" role="img" aria-label="Skizze eines Rebblatts"/>
  <ellipse class="sketch" cx="597" cy="476" rx="40" ry="40" role="img" aria-label="Skizze eines Rebblatts"/>

  <text class="serif bottler" x="340" y="467" text-anchor="middle">Abfüller</text>
  <text class="serif address" x="340" y="502" text-anchor="middle">Straße / PLZ / Ort / Tel.</text>
</svg>
</body>
</html>
```